Cover-Design für Buch gesucht
Die Designerin war sehr engagiert und hat innerhalb kürzester Zeit auf Änderungswünsche reagiert - und das so lange, so detailliert und so geduldig, bis wirklich alles gut war!
Zielgruppe
Ich bin niedergelassene Psychotherapeutin und schreibe nebenher als Hobby. Für mein erstes Buch, das ich im Selbstverlag bei Veltrano SPX veröffentlichen möchte, benötige ich ein aussagekräftiges, ausgefallenes, neugierig machendes Buchcover.
Zielgruppe sind hauptsächlich Krimi-Leser/innen und am Rande hoffentlich ein paar Fantasy-Leser/innen. Altersklasse vermutlich von ca. 20 bis 50 Jahre.
Aufgabenstellung
Das Buch ist eine Mischung aus Krimi und Fantasy. Wobei ich die Vampire ein Stück weit aus dem Bereich der Fantasy rausgeholt und „realistisch“ gemacht habe. Die Vampire sind quasi eine zweite – im Laufe der Evolution parallel zu den Menschen entwickelte – Art von Menschen. Sie werden geboren, leben in echt, können ganz normal verletzt werden und auch sterben. Sie leben in Symbiose mit den Menschen, trinken nachts, wenn die Menschen schlafen, deren Blut und spritzen danach ein hochregeneratives Serum in die Wunde, was die Wunde a) innerhalb kürzester Zeit heilen lässt und b) zusätzlich einige Krankheiten der Menschen heilen kann. Die Vampire haben noch immer ein paar spezielle Fähigkeiten (aber keine wirklich übernatürlichen Fähigkeiten mehr), sind z.B. stärker, attraktiver und deren Wunden heilen wegen ihrer regenerativen Eigenschaften schneller. All diese Fähigkeiten versuche ich „wissenschaftlich/medizinisch“ zu erklären – sofern man etwas nicht Existierendes und in unserer Realität nicht Machbares eben erklären kann.
Im Grunde handelt es sich also nicht mehr um klassische Fantasy, weil die Vampire ja einfach nur eine zweite Art von ganz „normalen“ Menschen sind. Insofern sollte das Buch-Cover vor allem in das Genre Krimi passen, dennoch irgendwie am Rande das Thema Vampir aufgreifen, so dass potentielle Leser erkennen, dass es sich eben nicht um einen ganz normalen Krimi handelt, sondern Vampire eine gewisse Rolle spielen.
Neben dem Kriminalfall (Kinder werden entführt, die Protagonisten müssen herausfinden, wer dies wieso gemacht hat) spielt die Freundschaft zwischen Henrike und Benno eine große Rolle, die sich langsam entwickelnde und intensiver werdende Schüler-Lehrer-Beziehung zwischen Henrike und Ole sowie die sich langsam entwickelnde Liebe zwischen Henrike und Kai. Die Geschichte ist also etwas „weicher“ und vielleicht von den zwischenmenschlichen Themen etwas tiefgründiger als ein einfacher, „knall..

```html
<!DOCTYPE html>
<html lang="de">
<head>
<meta charset="utf-8">
<title>Spurlos im Dunkel – Kriminalroman</title>
<link rel="stylesheet" href="https://fonts.googleapis.com/css2?family=Bebas+Neue&family=Ubuntu:wght@500&display=swap">
<style>
  :root {
    --cover-black: #000000;
    --blood-red: #c8001a;
    --title-white: #ffffff;
  }
  html, body {
    margin: 0;
    padding: 0;
    width: 750px;
    height: 1200px;
    overflow: hidden;
    background: var(--cover-black);
  }
  .book-cover {
    position: relative;
    width: 750px;
    height: 1200px;
    background: var(--cover-black);
    overflow: hidden;
  }
  .author-name {
    position: absolute;
    top: 45px;
    left: 0;
    width: 750px;
    margin: 0;
    text-align: center;
    font-family: "Ubuntu", "Helvetica Neue", Arial, sans-serif;
    font-weight: 500;
    font-size: 81px;
    letter-spacing: 4px;
    line-height: 1;
    color: var(--blood-red);
  }
  .cover-photo {
    position: absolute;
    left: 320px;
    top: 175px;
    width: 260px;
    height: 550px;
    border-radius: 40px;
    background:
      radial-gradient(ellipse 45% 30% at 55% 55%, rgba(140, 20, 30, 0.55), transparent 70%),
      radial-gradient(ellipse 40% 22% at 35% 40%, rgba(150, 115, 85, 0.45), transparent 70%),
      radial-gradient(ellipse 60% 70% at 50% 50%, #1c1414, var(--cover-black) 80%);
  }
  .title-art {
    position: absolute;
    left: 0;
    top: 0;
    width: 750px;
    height: 1200px;
  }
  .title-text {
    font-family: "Bebas Neue", "Oswald", Impact, sans-serif;
    font-size: 190px;
    fill: var(--title-white);
  }
  .genre-label {
    position: absolute;
    top: 1106px;
    left: 0;
    width: 750px;
    margin: 0;
    text-align: center;
    font-family: "Ubuntu", "Helvetica Neue", Arial, sans-serif;
    font-weight: 500;
    font-size: 44px;
    letter-spacing: 0.5px;
    line-height: 1;
    color: var(--blood-red);
  }
</style>
</head>
<body>
  <main class="book-cover">
    <p class="author-name">LENNART VOSS</p>

    <div class="cover-photo" role="img" aria-label="Foto: ein kleines Mädchen im roten Kleid mit einem Teddybären steht im Dunkeln"></div>

    <svg class="title-art" viewBox="0 0 750 1200" xmlns="http://www.w3.org/2000/svg" aria-labelledby="book-title">
      <title id="book-title">Spurlos im Dunkel</title>
      <text class="title-text" x="68" y="852" textLength="629" lengthAdjust="spacingAndGlyphs">SPURLOS</text>
      <text class="title-text" x="68" y="1020" textLength="622" lengthAdjust="spacingAndGlyphs">IM DUNKEL</text>
    </svg>

    <p class="genre-label">KRIMINALROMAN</p>
  </main>
</body>
</html>
```